Sophisticated, clean website reflecting my feminine, playful side to sell my abstract art,

I need a website no more than 3 pages to showcase my paintings, a little about me and some contact info. I do abstracts so looking for something a little edgy, yet feminine and current.
Updates

Hi there, These are some artists websites that I Iike: Marnelvoss.com (I like how airy it is) peterwallombry.com garethpolvens.com (I like how it scrolls) I'll need a place for a photo ( a headshot-i do not have it yet so I'll need to be able to upload that later) as well as an area for my bio. Also, it's important that I will be able to upload any new photos and descriptions easily so it should be user friendly. Lastly, I like in a sunny place so would like to have this seem upbeat and playful as that is how i like to paint. thanks-I'm trying to upload my photos now -

Target Market(s)

ppl ages 35-70 who want large scale art for their homes

Industry/Entity Type

art

Coding

Coded - Design and coding required

Number of Pages Required

3 page

Colors

Designer to choose colors to be used in the design.

Requirements
Must have
• photos of my art, a place for my bio, be easy to reach me. tasteful-nothing too "in your face" -my clients are pretty high end and organized. They like clean lines
Nice to have
• sophisticated background, muted tones in the back-similar clean font throughout-no cursive
Should not have
• too many dark areas. Too many blocks of color. Too serious.

```html
<!DOCTYPE html>
<html lang="en">
<head>
<meta charset="utf-8">
<title>Clara Wendell — Abstract Art</title>
<link rel="stylesheet" href="https://fonts.googleapis.com/css2?family=Raleway:wght@300;400&family=Questrial&display=swap">
<style>
  :root {
    --page-bg: #f5f5f5;
    --header-bg: #ffffff;
    --ink: #111111;
    --ink-soft: #3a3a3a;
    --rule: #cfcfcf;
    --accent-line: #333333;
    --frame-grey: #bdbdbd;
    --frame-dark: #7a7a7a;
    --control-bg: #000000;
    --control-ink: #ffffff;
  }
  * { margin: 0; padding: 0; box-sizing: border-box; }
  html, body { width: 1200px; height: 2746px; overflow: hidden; }
  body {
    position: relative;
    background: var(--page-bg);
    color: var(--ink);
    font-family: "Questrial", sans-serif;
  }
  .abs { position: absolute; }

  /* Header */
  .site-header { left: 0; top: 0; width: 1200px; height: 162px; background: var(--header-bg); }
  .site-title {
    left: 0; width: 1193px; top: 22px; text-align: center;
    font-family: "Raleway", sans-serif; font-weight: 400; font-size: 44px; letter-spacing: 1px;
  }
  .header-social { left: 941px; top: 38px; display: flex; align-items: center; gap: 8px; font-size: 16px; color: var(--ink-soft); white-space: nowrap; }
  .header-social .mark { width: 24px; height: 24px; border: 1.5px solid var(--ink-soft); border-radius: 6px; }
  .header-rule { left: 0; top: 101px; width: 1200px; height: 1px; background: var(--rule); }
  .main-nav { top: 121px; left: 0; width: 1200px; height: 40px; font-size: 16px; color: var(--ink-soft); }
  .main-nav a { position: absolute; transform: translateX(-50%); text-decoration: none; color: inherit; white-space: nowrap; }
  .nav-active-bar { left: 288px; top: 158px; width: 56px; height: 3px; background: var(--ink); }

  /* Hero */
  .hero-art {
    left: 0; top: 162px; width: 1200px; height: 648px;
    background: linear-gradient(110deg, #e6e2ea 0%, #3f9a55 22%, #2f7f6a 40%, #6aaa45 55%, #c9c080 70%, #2c6f78 82%, #4a3a2c 100%);
  }
  .hero-control { top: 788px; width: 66px; height: 42px; background: var(--control-bg); display: flex; align-items: center; justify-content: center; }

  /* About */
  .portrait-frame { left: 83px; top: 920px; width: 385px; height: 428px; border: 2px solid var(--frame-dark); padding: 8px; background: #fff; }
  .portrait-frame .portrait { width: 100%; height: 100%; background: linear-gradient(180deg, #dcdcdc 0%, #d6d6d6 60%, #a9c1d8 100%); }
  .section-title { font-family: "Raleway", sans-serif; font-weight: 400; color: var(--ink); white-space: nowrap; }
  .about-title { left: 530px; top: 930px; font-size: 50px; }
  .title-bar { height: 3px; background: var(--accent-line); }
  .about-copy { left: 530px; top: 1037px; width: 605px; font-family: "Raleway", sans-serif; font-size: 18.5px; line-height: 28px; color: var(--ink-soft); }
  .about-copy p + p { margin-top: 15px; }

  /* Gallery */
  .gallery-title { left: 0; width: 1181px; top: 1494px; text-align: center; font-size: 38px; }
  .gallery-frame { left: 228px; top: 1585px; width: 758px; height: 498px; border: 7px solid var(--frame-grey); background: #fff; padding: 7px; }
  .gallery-frame .artwork { width: 100%; height: 100%; background: linear-gradient(135deg, #b8692c 0%, #2d7a72 30%, #3a332d 55%, #e6e0d2 72%, #3d8a7a 100%); }
  .gallery-arrow { top: 1785px; }

  /* Contact */
  .contact-title { left: 0; width: 1188px; top: 2200px; text-align: center; font-size: 48px; }
  .contact-intro { left: 0; width: 1196px; top: 2289px; text-align: center; font-size: 19px; color: var(--ink-soft); }
  .contact-icon { width: 65px; height: 62px; border: 1.5px solid var(--ink-soft); background: #fff; display: flex; align-items: center; justify-content: center; }
  .contact-label { font-family: "Raleway", sans-serif; font-size: 18px; color: var(--ink-soft); white-space: nowrap; }
  .contact-value { font-family: "Raleway", sans-serif; font-size: 20px; color: var(--ink); white-space: nowrap; }

  /* Footer */
  .footer-rule { left: 0; top: 2653px; width: 1200px; height: 1px; background: var(--rule); }
  .site-footer { left: 0; width: 1222px; top: 2680px; text-align: center; font-size: 15px; color: var(--ink-soft); }
</style>
</head>
<body>
  <header class="site-header abs"></header>
  <h1 class="site-title abs">CLARA WENDELL</h1>
  <div class="header-social abs"><span class="mark"></span><span>@cwendellart</span></div>
  <div class="header-rule abs"></div>
  <nav class="main-nav abs">
    <a style="left:316px">HOME</a>
    <a style="left:494px">ABOUT ME</a>
    <a style="left:685px">GALLERY</a>
    <a style="left:874px">CONTACT</a>
  </nav>
  <div class="nav-active-bar abs"></div>

  <div class="hero-art abs" role="img" aria-label="Slideshow of an abstract painting in greens, teal and ochre brushstrokes"></div>
  <div class="hero-control abs" style="left:944px">
    <svg width="16" height="18" viewBox="0 0 16 18"><polygon points="14,0 14,18 0,9" fill="var(--control-ink)"/></svg>
  </div>
  <div class="hero-control abs" style="left:1020px">
    <svg width="16" height="18" viewBox="0 0 16 18"><polygon points="2,0 2,18 16,9" fill="var(--control-ink)"/></svg>
  </div>

  <section>
    <div class="portrait-frame abs"><div class="portrait" role="img" aria-label="Artist headshot placeholder"></div></div>
    <h2 class="section-title about-title abs">ABOUT ME</h2>
    <div class="title-bar abs" style="left:533px;top:1002px;width:67px"></div>
    <div class="about-copy abs">
      <p>Lorem ipsum dolor sit amet, consectetur adipiscing elit, sed do eius-mod tempor incididunt ut labore et dolore magna aliqua. Ut enim ad minim veniam, quis nostrud exercitation</p>
      <p>Duis aute irure dolor in reprehenderit in voluptate velit esse cillum dolore eu fugiat nulla pariatur. Excepteur sint occaecat cupidatat non proident, sunt in culpa qui officia deserunt mollit anim id est laborum</p>
      <p>Sed ut perspiciatis unde pariatur. Excepteur sint occaecat cupidatat non proident, sunt in culpa qui officia deserunt mollit anim id est laborum.Sed ut persmollit anim id est laborum.</p>
    </div>
  </section>

  <section>
    <h2 class="section-title gallery-title abs">PHOTO GALLERY</h2>
    <div class="title-bar abs" style="left:583px;top:1543px;width:64px"></div>
    <svg class="gallery-arrow abs" style="left:151px" width="36" height="66" viewBox="0 0 36 66"><polyline points="34,1 2,33 34,65" fill="none" stroke="var(--ink-soft)" stroke-width="2"/></svg>
    <div class="gallery-frame abs"><div class="artwork" role="img" aria-label="Abstract painting with orange, teal, black and white burst of strokes"></div></div>
    <svg class="gallery-arrow abs" style="left:1018px" width="36" height="66" viewBox="0 0 36 66"><polyline points="2,1 34,33 2,65" fill="none" stroke="var(--ink-soft)" stroke-width="2"/></svg>
  </section>

  <section>
    <h2 class="section-title contact-title abs">CONTACT US</h2>
    <div class="title-bar abs" style="left:555px;top:2263px;width:92px"></div>
    <p class="contact-intro abs">Please get in touch with me on below details.</p>

    <div class="contact-icon abs" style="left:168px;top:2380px">
      <svg width="32" height="24" viewBox="0 0 32 24"><rect x="1" y="1" width="30" height="22" fill="none" stroke="var(--ink-soft)" stroke-width="1.4"/><polyline points="1,1 16,14 31,1" fill="none" stroke="var(--ink-soft)" stroke-width="1.4"/><line x1="1" y1="23" x2="12" y2="11" stroke="var(--ink-soft)" stroke-width="1.4"/><line x1="31" y1="23" x2="20" y2="11" stroke="var(--ink-soft)" stroke-width="1.4"/></svg>
    </div>
    <div class="contact-label abs" style="left:168px;top:2457px">Email address</div>
    <div class="contact-value abs" style="left:168px;top:2486px">clarawendell@info.com</div>

    <div class="contact-icon abs" style="left:541px;top:2377px">
      <svg width="32" height="32" viewBox="0 0 32 32"><path d="M7 3 L12 3 L14 10 L10 13 Q13 20 19 23 L22 19 L29 21 L29 26 Q28 30 24 29 Q10 25 4 9 Q3 4 7 3 Z" fill="none" stroke="var(--ink-soft)" stroke-width="1.4" stroke-linejoin="round"/></svg>
    </div>
    <div class="contact-label abs" style="left:539px;top:2457px">Phone number</div>
    <div class="contact-value abs" style="left:539px;top:2486px">(555) 218 4630</div>

    <div class="contact-icon abs" style="left:846px;top:2375px"></div>
    <div class="contact-label abs" style="left:845px;top:2457px">Follow me on social media</div>
    <div class="contact-label abs" style="left:842px;top:2484px">@cwendellart</div>
  </section>

  <div class="footer-rule abs"></div>
  <footer class="site-footer abs">© 2022 Clara Wendell &nbsp; All Rights Reserved</footer>
</body>
</html>
```